Alcohol brand needs design for gift tin packaging

We need a new design for the gift tins for our vodka brand. The bottles are in the shape of an oil barrel and the tins are also in the same shape. We would like to see the use of our logo. The gift tin needs to have a premium look.
Images of our bottles, logo and the gift tin are attached.

```html
<!DOCTYPE html>
<html lang="en">
<head>
<meta charset="UTF-8">
<title>Iron Drum Vodka – Gift Tin</title>
<link href="https://fonts.googleapis.com/css2?family=Oswald:wght@500;700&family=Special+Elite&display=swap" rel="stylesheet">
<style>
  :root {
    --paper: #ffffff;
    --tin-black: #141414;
    --tin-rib: #262626;
    --gold-light: #e9c65a;
    --gold: #c99a3b;
    --bronze: #8a5a2b;
    --rust: #6b3d1c;
    --silver: #b9b9b9;
    --ink: #231409;
  }
  * { margin: 0; padding: 0; box-sizing: border-box; }
  html, body { width: 1149px; height: 1200px; overflow: hidden; background: var(--paper); }
  .canvas { position: relative; width: 1149px; height: 1200px; }

  .brand-mark {
    position: absolute; top: 110px; left: 0; width: 100%;
    display: flex; justify-content: center; align-items: center; gap: 18px;
  }
  .brand-mark__dot { width: 34px; height: 34px; border-radius: 50%; background: var(--rust); }
  .brand-mark__name {
    font-family: "Oswald", sans-serif; font-weight: 700; font-size: 64px;
    letter-spacing: 4px; color: var(--rust); text-transform: uppercase;
  }

  .tin-front {
    position: absolute; left: 262px; top: 300px; width: 625px; height: 850px;
    background: linear-gradient(90deg, #0b0b0b 0%, var(--tin-black) 20%, #1e1e1e 50%, var(--tin-black) 80%, #0b0b0b 100%);
    border-radius: 22px; overflow: hidden;
  }
  .tin-front__rib { position: absolute; left: 0; width: 100%; height: 6px; background: var(--tin-rib); }
  .tin-front__rib--upper { top: 300px; }
  .tin-front__rib--lower { top: 560px; }
  .tin-front__rib--base { top: 760px; }

  .tin-front__name, .tin-front__product, .tin-front__slogan {
    position: absolute; left: 0; width: 100%; text-align: center;
    font-family: "Oswald", sans-serif; font-weight: 700; color: var(--gold); text-transform: uppercase;
  }
  .tin-front__name { top: 70px; font-size: 104px; letter-spacing: 4px; }
  .tin-front__product { top: 215px; font-size: 70px; letter-spacing: 3px; color: var(--bronze); }

  .tin-front__seal { position: absolute; left: 60px; top: 330px; width: 505px; height: 260px; }

  .tin-front__variety {
    position: absolute; top: 612px; left: 0; width: 100%; text-align: center;
    font-family: "Special Elite", monospace; font-size: 32px; color: var(--silver);
  }
  .tin-front__slogan { top: 655px; font-size: 64px; letter-spacing: 3px; color: var(--bronze); }
  .tin-front__origin {
    position: absolute; top: 785px; left: 0; width: 100%; text-align: center;
    font-family: "Special Elite", monospace; font-size: 30px; letter-spacing: 2px; color: var(--silver);
  }
</style>
</head>
<body>
<main class="canvas">
  <header class="brand-mark">
    <span class="brand-mark__dot"></span>
    <span class="brand-mark__name">Iron Drum</span>
  </header>

  <section class="tin-front">
    <div class="tin-front__rib tin-front__rib--upper"></div>
    <div class="tin-front__rib tin-front__rib--lower"></div>
    <div class="tin-front__rib tin-front__rib--base"></div>

    <h1 class="tin-front__name">Iron Drum</h1>
    <h2 class="tin-front__product">Vodka</h2>

    <svg class="tin-front__seal" viewBox="0 0 505 260">
      <defs>
        <linearGradient id="band" x1="0" x2="1">
          <stop offset="0" stop-color="#7a4a22"/>
          <stop offset="0.5" stop-color="#c99a3b"/>
          <stop offset="1" stop-color="#7a4a22"/>
        </linearGradient>
        <radialGradient id="medal" cx="0.4" cy="0.35" r="0.7">
          <stop offset="0" stop-color="#f3d877"/>
          <stop offset="0.6" stop-color="#d6a742"/>
          <stop offset="1" stop-color="#8a5a2b"/>
        </radialGradient>
      </defs>
      <polygon points="0,55 505,30 505,195 0,215" fill="url(#band)"/>
      <circle cx="252" cy="130" r="125" fill="url(#medal)" role="img" aria-label="Illustration of a horned skull in gold and dark brown"/>
      <text x="65" y="112" text-anchor="middle" font-family="Oswald, sans-serif" font-weight="700" font-size="38" fill="#231409">SINCE</text>
      <text x="65" y="168" text-anchor="middle" font-family="Oswald, sans-serif" font-weight="700" font-size="58" fill="#231409">2017</text>
      <text x="440" y="112" text-anchor="middle" font-family="Oswald, sans-serif" font-weight="700" font-size="58" fill="#231409">40%</text>
      <text x="440" y="150" text-anchor="middle" font-family="Oswald, sans-serif" font-weight="500" font-size="28" fill="#231409">ALCOHOL</text>
    </svg>

    <p class="tin-front__variety">Single Malt</p>
    <p class="tin-front__slogan">Drink Cautiously</p>
    <p class="tin-front__origin">PREMIUM AUSTRALIAN VODKA</p>
  </section>
</main>
</body>
</html>
```